Dietitian needs awesome business card

I need a contemporary design that's eye catching but professional.
My card is to given to doctors, specialists and patients alike.
I manage patients with chronic diseases
I have uploaded my logo and current business card, I would also like the other Certified Clinical Nutritionist logo incorporated into the design

Target Market(s)

Doctors, specialists and patients

Industry/Entity Type

Healthcare

Contact Information for Business Card

www.brightfieldnutrition.com.au
Ph: 0427 561 903
Fax: 6457 2183
email: marcus.k.diet@fernmail.com
Space on the back of the card with: Appointment date, Appointment time and appointment location

Font styles to use
Serif

Colors
fbee3e
876aae
ffc214

Requirements
Must have
• My Logo
• Certified Clinical Nutritionist Logo
• My 4 locations - Pinebrook Medical Centre, North Corrin Health, Hollis Medical, Ashcombe Doctors Surgery
Nice to have
• I like the colours in my current business card

```html
<!DOCTYPE html>
<html lang="en">
<head>
<meta charset="utf-8">
<title>Brightfield Nutrition – Business Card</title>
<link href="https://fonts.googleapis.com/css2?family=Roboto:wght@400;500;700&display=swap" rel="stylesheet">
<style>
  :root {
    --navy: #1b1f8a;
    --blue: #0a74b8;
    --sky: #0aa0d6;
    --green: #7cbc22;
    --green-dark: #2f9a3a;
    --ink: #444a52;
    --rule: #cfd3d6;
    --page: #e9ebee;
    --card: #ffffff;
  }
  * { margin: 0; padding: 0; box-sizing: border-box; }
  html, body { width: 1200px; height: 987px; overflow: hidden; }
  body {
    background: var(--page);
    font-family: "Roboto", Arial, sans-serif;
    position: relative;
  }
  .card {
    position: absolute;
    left: 293px;
    width: 525px;
    height: 300px;
    transform: scale(1.1719);
    transform-origin: top left;
    background: var(--card);
    border-radius: 16px;
    overflow: hidden;
    box-shadow: 0 2px 6px rgba(0,0,0,0.18);
  }
  .card--front { top: 128px; }
  .card--back { top: 507px; }

  .front-waves { position: absolute; inset: 0; width: 525px; height: 300px; }

  .identity {
    position: absolute; right: 24px; top: 22px;
    text-align: right; color: #fff;
  }
  .identity__name { font-size: 18px; font-weight: 500; line-height: 22px; }
  .identity__role { font-size: 14px; line-height: 19px; }

  .brand {
    position: absolute; left: 32px; top: 200px;
    display: flex; align-items: center; gap: 8px;
  }
  .brand__dot { width: 26px; height: 26px; border-radius: 50%; background: var(--blue); }
  .brand__name { font-size: 20px; font-weight: 400; color: var(--navy); white-space: nowrap; }

  .divider {
    position: absolute; left: 247px; top: 156px;
    width: 1px; height: 88px; background: var(--rule);
  }

  .contacts { position: absolute; left: 268px; top: 159px; list-style: none; }
  .contacts li {
    display: flex; align-items: center; gap: 9px;
    height: 20px; font-size: 14px; color: var(--ink);
  }
  .contacts svg { width: 15px; height: 15px; fill: var(--navy); flex: none; }

  .back-photo {
    position: absolute; inset: 0;
    background:
      radial-gradient(ellipse at 30% 30%, rgba(214,228,208,0.55), transparent 60%),
      radial-gradient(ellipse at 80% 55%, rgba(224,234,216,0.5), transparent 55%),
      linear-gradient(180deg, #f4f7f2, #fbfcfa);
  }
  .appointment { position: absolute; inset: 0; }
  .appointment__title {
    position: absolute; top: 26px; width: 100%;
    text-align: center; font-size: 17px; font-weight: 500; color: var(--navy);
  }
  .appointment__line {
    position: absolute; left: 36px; width: 452px; height: 1px; background: var(--rule);
  }
  .appointment__when {
    position: absolute; left: 36px; top: 190px; width: 452px;
    display: flex; align-items: baseline; font-size: 14px; color: var(--navy);
  }
  .fill { border-bottom: 1px dotted var(--navy); height: 1px; margin: 0 5px; align-self: flex-end; margin-bottom: 4px; }
  .fill--date { width: 182px; margin-left: 12px; }
  .fill--time { width: 117px; }
  .ampm { font-size: 11px; }
  .locations {
    position: absolute; left: 37px; top: 226px; width: 460px;
    display: grid; grid-template-columns: 261px 1fr; row-gap: 3px;
    list-style: none; font-size: 14px; color: var(--ink);
  }
  .locations li { display: flex; align-items: center; gap: 6px; line-height: 17px; }
  .box { width: 11px; height: 11px; border: 1.3px solid var(--navy); }
</style>
</head>
<body>

<section class="card card--front">
  <svg class="front-waves" viewBox="0 0 525 300" aria-hidden="true">
    <defs>
      <linearGradient id="headerFill" x1="0" y1="0" x2="1" y2="0.3">
        <stop offset="0" stop-color="#1b1f8a"/>
        <stop offset="0.55" stop-color="#0a79be"/>
        <stop offset="1" stop-color="#1b1f8a"/>
      </linearGradient>
      <linearGradient id="greenBand" x1="0" y1="1" x2="1" y2="0">
        <stop offset="0" stop-color="#2f9a3a"/>
        <stop offset="0.5" stop-color="#8cc63f"/>
        <stop offset="1" stop-color="#c8e07a"/>
      </linearGradient>
    </defs>
    <path d="M0 0 H525 V118 C470 124 400 118 320 96 C230 70 150 36 90 46 C45 54 15 90 0 125 Z" fill="url(#headerFill)"/>
    <path d="M0 170 C20 110 60 70 120 66 C190 62 250 90 330 110 C400 126 460 130 525 122" fill="none" stroke="url(#greenBand)" stroke-width="7"/>
    <path d="M0 138 C25 85 70 58 130 56 C210 54 270 92 350 112 C420 128 470 128 525 118" fill="none" stroke="#ffffff" stroke-width="5"/>
    <path d="M0 158 C25 102 70 70 130 66 C200 62 260 96 340 116 C410 130 470 130 525 124" fill="none" stroke="#1b3f9e" stroke-width="3"/>
  </svg>

  <header class="identity">
    <p class="identity__name">Marcus Kellaway</p>
    <p class="identity__role">Certified Clinical Nutritionist</p>
    <p class="identity__role">Nutritionist &amp; Chef</p>
  </header>

  <div class="brand">
    <span class="brand__dot"></span>
    <span class="brand__name">Brightfield Nutrition</span>
  </div>

  <div class="divider"></div>

  <ul class="contacts">
    <li><svg viewBox="0 0 16 16"><path d="M3.5 1.5l2.3 0 1 3.2-1.5 1.2c.8 1.8 2.1 3.1 3.9 3.9l1.2-1.5 3.2 1v2.3c0 .8-.7 1.4-1.5 1.4C6.9 13 3 9.1 2.1 3c0-.8.6-1.5 1.4-1.5z"/></svg>0427 561 903</li>
    <li><svg viewBox="0 0 16 16"><path d="M4 1h8v4H4z M1 6h14v6h-2v3H3v-3H1z M4.5 10v3.5h7V10z"/></svg>6457 2183</li>
    <li><svg viewBox="0 0 16 16"><path d="M1 3h14v10H1z" /><path d="M1.5 3.5L8 9l6.5-5.5" fill="none" stroke="#fff" stroke-width="1.3"/></svg>marcus.k.diet@fernmail.com</li>
    <li><svg viewBox="0 0 16 16"><circle cx="8" cy="8" r="7"/><path d="M4 5c2 0 2 2 4 2s1 3 3 3M9 2.5c-1 1.5 1 2.5 3 2" fill="none" stroke="#fff" stroke-width="1.4"/></svg>www.brightfieldnutrition.com.au</li>
  </ul>
</section>

<section class="card card--back">
  <div class="back-photo" role="img" aria-label="Faint photograph of fresh green vegetables"></div>
  <div class="appointment">
    <h2 class="appointment__title">YOUR APPOINTMENT</h2>
    <div class="appointment__line" style="top:71px"></div>
    <div class="appointment__line" style="top:101px"></div>
    <div class="appointment__line" style="top:131px"></div>
    <div class="appointment__line" style="top:161px"></div>
    <div class="appointment__when">
      <span>Date :</span><span class="fill fill--date"></span>
      <span>Time :</span><span class="fill fill--time"></span>
      <span class="ampm">AM/PM</span>
    </div>
    <ul class="locations">
      <li><span class="box"></span>Pinebrook Medical Centre</li>
      <li><span class="box"></span>Hollis Medical</li>
      <li><span class="box"></span>North Corrin Health</li>
      <li><span class="box"></span>Ashcombe Doctors Surgery</li>
    </ul>
  </div>
</section>

</body>
</html>
```